Verloe Partners
Global Real Estate Investing
Verloe Partners -
Creative Brief
Modern
Tomas Verloe
President
24870 Dallow Road 2nd Floor Southgate MI 48273
tverloe@verloepartners.example
www.verloepartners.example

```html
<!DOCTYPE html>
<html lang="en">
<head>
<meta charset="utf-8">
<title>Verloe Partners — Stationery</title>
<link href="https://fonts.googleapis.com/css2?family=Montserrat:wght@400;600;700;800&display=swap" rel="stylesheet">
<style>
  :root {
    --backdrop: #3b3b3d;
    --paper: #ffffff;
    --navy: #2c2f7c;
    --ink: #4a4a55;
    --muted: #8a8a94;
    --rule: #d6d6dc;
    --field: #e4e4e8;
  }
  * { box-sizing: border-box; margin: 0; padding: 0; }
  html, body { width: 1200px; height: 509px; overflow: hidden; }
  body {
    background: var(--backdrop);
    font-family: "Montserrat", Arial, sans-serif;
    color: var(--ink);
    position: relative;
  }
  .sheet {
    position: absolute;
    background: var(--paper);
    overflow: hidden;
  }
  .brand { display: flex; flex-direction: column; align-items: center; gap: 3px; }
  .brand-dot { border-radius: 50%; background: var(--navy); }
  .brand-name {
    font-weight: 800; color: var(--navy); text-transform: uppercase;
    letter-spacing: .5px; line-height: 1;
  }

  /* Business card front */
  .card-front { left: 5px; top: 12px; width: 115px; height: 78px; }
  .card-front .brand { position: absolute; left: 10px; bottom: 10px; align-items: flex-start; }
  .card-front .brand-dot { width: 12px; height: 12px; }
  .card-front .brand-name { font-size: 11px; }

  /* Business card back */
  .card-back { left: 130px; top: 12px; width: 112px; height: 78px; padding: 9px 8px; }
  .card-back .person { font-size: 5.5px; font-weight: 700; color: var(--navy); text-transform: uppercase; }
  .card-back .role { font-size: 4px; color: var(--muted); margin-top: 1px; }
  .card-back .contact { position: absolute; left: 8px; bottom: 8px; font-size: 3.6px; line-height: 1.45; color: var(--ink); }
  .card-back .brand { position: absolute; right: 8px; top: 8px; }
  .card-back .brand-dot { width: 7px; height: 7px; }
  .card-back .brand-name { font-size: 5px; }

  /* Envelope back */
  .envelope { left: 24px; top: 137px; width: 348px; height: 170px; }
  .envelope svg { position: absolute; inset: 0; }
  .envelope .brand { position: absolute; left: 50%; top: 38px; transform: translateX(-50%); }
  .envelope .brand-dot { width: 18px; height: 18px; }
  .envelope .brand-name { font-size: 9px; }

  /* Envelope front */
  .envelope-front { left: 24px; top: 336px; width: 348px; height: 132px; }
  .envelope-front .brand { position: absolute; left: 12px; top: 16px; align-items: flex-start; }
  .envelope-front .brand-dot { width: 16px; height: 16px; }
  .envelope-front .brand-name { font-size: 13px; }
  .envelope-front .return { position: absolute; right: 14px; bottom: 8px; font-size: 4px; color: var(--ink); }

  /* Letterhead */
  .letterhead { left: 396px; top: 12px; width: 389px; height: 468px; }
  .letterhead .brand { position: absolute; left: 50%; top: 36px; transform: translateX(-50%); }
  .letterhead .brand-dot { width: 20px; height: 20px; }
  .letterhead .brand-name { font-size: 12px; }
  .letterhead .footer {
    position: absolute; left: 0; right: 0; bottom: 20px;
    text-align: center; font-size: 4.2px; line-height: 1.6; color: var(--ink);
  }

  /* Fax */
  .fax { left: 816px; top: 12px; width: 365px; height: 468px; }
  .fax .brand { position: absolute; left: 14px; top: 14px; }
  .fax .brand-dot { width: 12px; height: 12px; }
  .fax .brand-name { font-size: 6px; }
  .fax .address { position: absolute; left: 50px; top: 14px; font-size: 4px; line-height: 1.5; }
  .fax .contact { position: absolute; left: 150px; top: 14px; font-size: 4px; line-height: 1.5; }
  .fax .title { position: absolute; right: 22px; top: 18px; font-size: 17px; font-weight: 700; color: var(--navy); letter-spacing: 1px; }
  .fax .form {
    position: absolute; left: 14px; right: 14px; top: 56px;
    display: grid; grid-template-columns: 1fr 1fr; gap: 4px 8px;
  }
  .fax .field { display: flex; height: 13px; font-size: 4.2px; }
  .fax .field b { width: 28px; background: var(--navy); color: #fff; font-weight: 600; display: flex; align-items: center; padding-left: 3px; }
  .fax .field span { flex: 1; background: var(--field); }
  .fax .checks {
    position: absolute; left: 14px; right: 14px; top: 136px;
    display: flex; justify-content: space-between; font-size: 4.2px;
    border-top: 1px solid var(--rule); padding-top: 8px;
  }
  .fax .checks span::before {
    content: ""; display: inline-block; width: 5px; height: 5px;
    border: 0.6px solid var(--muted); margin-right: 3px; vertical-align: -1px;
  }
</style>
</head>
<body>

  <div class="sheet card-front">
    <div class="brand"><div class="brand-dot"></div><div class="brand-name">Verloe</div></div>
  </div>

  <div class="sheet card-back">
    <p class="person">Tomas Verloe</p>
    <p class="role">President</p>
    <div class="brand"><div class="brand-dot"></div><div class="brand-name">Verloe</div></div>
    <p class="contact">
      24870 Dallow Road 2nd Floor<br>Southgate MI 48273<br>
      T 555 014 2001<br>tverloe@verloepartners.example<br>www.verloepartners.example
    </p>
  </div>

  <div class="sheet envelope">
    <svg width="348" height="170" viewBox="0 0 348 170" aria-hidden="true">
      <polyline points="0,0 174,78 348,0" fill="none" stroke="#d6d6dc" stroke-width="1"/>
      <polyline points="0,170 140,72" fill="none" stroke="#e4e4e8" stroke-width="1"/>
      <polyline points="348,170 208,72" fill="none" stroke="#e4e4e8" stroke-width="1"/>
    </svg>
    <div class="brand"><div class="brand-dot"></div><div class="brand-name">Verloe</div></div>
  </div>

  <div class="sheet envelope-front">
    <div class="brand"><div class="brand-dot"></div><div class="brand-name">Verloe</div></div>
    <p class="return">24870 Dallow Road 2nd Floor Southgate MI 48273</p>
  </div>

  <div class="sheet letterhead">
    <div class="brand"><div class="brand-dot"></div><div class="brand-name">Verloe</div></div>
    <p class="footer">
      T 555 014 2001 · F 555 014 2002<br>
      24870 Dallow Road 2nd Floor Southgate MI 48273<br>
      tverloe@verloepartners.example · www.verloepartners.example
    </p>
  </div>

  <div class="sheet fax">
    <div class="brand"><div class="brand-dot"></div><div class="brand-name">Verloe</div></div>
    <p class="address">24870 Dallow Road<br>2nd Floor<br>Southgate MI 48273</p>
    <p class="contact">T 555 014 2001<br>F 555 014 2002<br>tverloe@verloepartners.example</p>
    <h1 class="title">FAX</h1>
    <div class="form">
      <div class="field"><b>To</b><span></span></div>
      <div class="field"><b>From</b><span></span></div>
      <div class="field"><b>Fax</b><span></span></div>
      <div class="field"><b>Pages</b><span></span></div>
      <div class="field"><b>Phone</b><span></span></div>
      <div class="field"><b>Date</b><span></span></div>
      <div class="field"><b>Re</b><span></span></div>
      <div class="field"><b>CC</b><span></span></div>
    </div>
    <div class="checks">
      <span>Urgent</span><span>For Review</span><span>Please Comment</span><span>Please Reply</span><span>Please Recycle</span>
    </div>
  </div>

</body>
</html>
```